Clear Harbor Business card

We are a company that owns 2 compliance software programs for TV, Radio and Cable industries as well as an online job board. We need a professional business card that incorproates all three logos.

```html
<!DOCTYPE html>
<html lang="en">
<head>
<meta charset="utf-8">
<title>Clear Harbor Business Card</title>
<link href="https://fonts.googleapis.com/css2?family=Mulish:wght@400;600;700&display=swap" rel="stylesheet">
<style>
  :root {
    --backdrop: #8b8b8b;
    --card: #ffffff;
    --ink: #1a1a1a;
    --navy: #1f1f63;
    --sky: #2a7fc4;
    --rule: #8a8a8a;
  }
  html, body {
    margin: 0;
    width: 1200px;
    height: 1200px;
    overflow: hidden;
    background: var(--backdrop);
    font-family: "Mulish", sans-serif;
  }
  .card {
    position: absolute;
    top: 310px;
    width: 364px;
    height: 594px;
    background: var(--card);
    box-shadow: 3px 4px 6px rgba(0,0,0,0.35);
    overflow: hidden;
  }
  .card--front { left: 234px; }
  .card--back { left: 627px; width: 369px; }

  .brand-row {
    position: absolute;
    display: flex;
    align-items: center;
    justify-content: center;
    color: var(--navy);
    font-weight: 700;
    white-space: nowrap;
  }
  .brand {
    display: flex;
    flex-direction: column;
    line-height: 1.05;
  }
  .brand--jobs {
    flex-direction: row;
    align-items: center;
    color: var(--sky);
  }
  .brand__stack { display: flex; flex-direction: column; }
  .brand-dot {
    border-radius: 50%;
    background: var(--sky);
    flex: none;
  }
  .brand-divider {
    width: 2px;
    align-self: stretch;
    background: var(--navy);
  }

  /* front logo row */
  .card--front .brand-row {
    top: 155px;
    left: 28px;
    width: 308px;
    height: 58px;
    font-size: 13px;
  }
  .card--front .brand { padding: 0 8px; }
  .card--front .brand--jobs { gap: 5px; }
  .card--front .brand-dot { width: 14px; height: 14px; }

  /* back logo column */
  .card--back .brand-row {
    left: 185px;
    top: 295px;
    width: 470px;
    height: 90px;
    margin-left: -235px;
    margin-top: -45px;
    transform: rotate(-90deg);
    font-size: 22px;
  }
  .card--back .brand { padding: 0 14px; }
  .card--back .brand--jobs { gap: 8px; }
  .card--back .brand-dot { width: 26px; height: 26px; }

  .contact {
    position: absolute;
    left: 0;
    top: 343px;
    width: 364px;
    text-align: center;
    color: var(--ink);
  }
  .contact__name {
    margin: 0;
    font-size: 21px;
    font-weight: 700;
    letter-spacing: 0.5px;
    line-height: 1.2;
  }
  .contact__role {
    margin: 0;
    font-size: 17px;
    line-height: 1.25;
  }
  .contact__rule {
    width: 208px;
    height: 1px;
    background: var(--rule);
    margin: 8px auto 9px;
    border: 0;
  }
  .contact__lines {
    margin: 0;
    font-size: 17px;
    line-height: 21.5px;
  }
  .contact__lines b { font-weight: 700; }
  .contact__web { font-weight: 700; }
</style>
</head>
<body>
  <section class="card card--front">
    <div class="brand-row">
      <span class="brand"><span>Clear Harbor</span><span>Air</span></span>
      <span class="brand-divider"></span>
      <span class="brand"><span>Clear Harbor</span><span>Cable</span></span>
      <span class="brand-divider"></span>
      <span class="brand brand--jobs"><span class="brand-dot"></span><span class="brand__stack"><span>StageCall</span><span>Jobs</span></span></span>
    </div>

    <div class="contact">
      <p class="contact__name">DANIEL MARSH</p>
      <p class="contact__role">Managing Director</p>
      <hr class="contact__rule">
      <p class="contact__lines">
        <b>P:</b> 044-555 010 200<br>
        <b>M:</b> 044-555 010 201<br>
        <b>E:</b> hello@clearharbor.com<br>
        <span class="contact__web">www.clearharbor.com</span>
      </p>
      <hr class="contact__rule">
      <p class="contact__lines">
        48 Quay Street<br>
        Portland, 10452.
      </p>
    </div>
  </section>

  <section class="card card--back">
    <div class="brand-row">
      <span class="brand"><span>Clear Harbor</span><span>Air</span></span>
      <span class="brand-divider"></span>
      <span class="brand"><span>Clear Harbor</span><span>Cable</span></span>
      <span class="brand-divider"></span>
      <span class="brand brand--jobs"><span class="brand-dot"></span><span class="brand__stack"><span>StageCall</span><span>Jobs</span></span></span>
    </div>
  </section>
</body>
</html>
```